Mental Health care Company in Washington DC

We are a new mental health care services provider in Washington DC. Please look at these sites.
https://brightwaterfamilysupport.com
https://www.quietharborinc.com
https://willowgate-dc.org/
https://www.tidepathdc.com
https://www.thelanternofdc.com

```html
<!DOCTYPE html>
<html lang="en">
<head>
<meta charset="utf-8">
<title>Lumen Health Services</title>
<link href="https://fonts.googleapis.com/css2?family=Poppins:wght@400;500;600;700;800&display=swap" rel="stylesheet">
<style>
:root{
  --navy:#0c1f3f;
  --orange:#f5a35c;
  --teal:#8fd3d6;
  --grey:#ecebec;
  --text:#2b2f3a;
  --white:#ffffff;
}
*{margin:0;padding:0;box-sizing:border-box}
html,body{width:1200px;height:3436px;overflow:hidden}
body{font-family:'Poppins',sans-serif;color:var(--text);background:var(--white);position:relative}
.abs{position:absolute}
.topbar{left:0;top:0;width:1200px;height:45px;background:var(--orange);font-size:12px;font-weight:500;color:var(--navy)}
.topbar span{position:absolute;top:14px;display:flex;align-items:center;gap:8px}
.flag{width:26px;height:16px;background:#cfd6e6;border:1px solid #9aa5c0;display:inline-block}
.nav{left:0;top:45px;width:1200px;height:87px;background:var(--white)}
.logo{display:flex;align-items:center;gap:8px;font-weight:500;color:var(--navy);white-space:nowrap}
.logo .dot{width:12px;height:12px;border-radius:50%;background:var(--orange)}
.nav .logo{position:absolute;left:89px;top:24px;font-size:32px}
.menu{position:absolute;left:366px;top:35px;display:flex;gap:18px;font-size:14px;font-weight:600;color:var(--navy);align-items:center}
.btn-navy{position:absolute;left:988px;top:22px;width:123px;height:44px;border-radius:22px;background:var(--navy);color:#fff;font-size:12px;font-weight:600;display:flex;align-items:center;justify-content:center}
.hero-photo{left:0;top:132px;width:1200px;height:612px;border-bottom-right-radius:190px 280px;background:linear-gradient(90deg,#f6f7f8 0%,#e9ebec 30%,#cdb9a2 55%,#a47d55 72%,#c99c37 85%,#8a6a4a 100%)}
.hero-title{left:89px;top:192px;font-size:88px;line-height:88px;font-weight:800;color:var(--navy);letter-spacing:-2px}
.hero-text{left:89px;top:377px;width:520px;font-size:14.5px;line-height:20px;color:var(--navy)}
.btn-orange{background:var(--orange);color:#fff;font-weight:600;font-size:12px;display:flex;align-items:center;justify-content:center;border-radius:24px}
.dots{display:flex;gap:8px;align-items:center}
.dots i{width:10px;height:10px;border-radius:5px;background:var(--navy);display:block}
.dots i.on{width:30px}
.h2{font-weight:700;color:var(--navy);font-size:36px;line-height:40px}
.body{font-size:13.5px;line-height:19.5px;color:var(--text)}
.center{text-align:center}
.photo-card{border-bottom-right-radius:80px}
.stat{width:220px;text-align:center;font-size:14px;line-height:19.5px}
.stat b{display:block;font-size:36px;font-weight:600;line-height:44px;margin-bottom:12px}
.divider{width:1px;height:112px;background:#c9c9c9}
.services-bg{left:0;top:1599px;width:1200px;height:718px;background:var(--grey);border-bottom-left-radius:520px 160px}
.card{width:271px;height:436px;background:#fff;border-radius:18px;overflow:hidden}
.card .img{height:232px}
.card h3{margin:20px 0 0 29px;font-size:22px;line-height:27px;font-weight:700;color:var(--navy)}
.card p{margin:10px 20px 0 31px;font-size:13px;line-height:19.5px}
.card .more{position:absolute;left:31px;top:385px;display:flex;align-items:center;gap:22px;font-size:12px;font-weight:600;color:var(--orange)}
.more .circ{width:26px;height:26px;border-radius:50%;background:var(--orange);display:flex;align-items:center;justify-content:center}
.checks{display:grid;grid-template-columns:227px 260px;row-gap:8px;font-size:13.5px;font-weight:500;color:var(--navy)}
.checks div{display:flex;align-items:center;gap:8px;white-space:nowrap}
.quote-mark{left:500px;top:2840px;font-size:300px;line-height:300px;font-weight:800;color:var(--orange);opacity:.55;font-family:Georgia,serif}
.footer-nav{display:flex;gap:18px;font-size:14px;font-weight:600;color:#fff;white-space:nowrap}
.social{width:34px;height:34px;border-radius:50%;background:#1e3155}
</style>
</head>
<body>

<header>
  <div class="abs topbar">
    <span style="left:89px"><svg width="12" height="12" viewBox="0 0 12 12"><circle cx="6" cy="6" r="5.5" fill="var(--navy)"/><path d="M6 3v3.2l2 1.3" stroke="#f5a35c" stroke-width="1.3" fill="none"/></svg>Our Helpline: (+1) 20 555 0199</span>
    <span style="left:340px"><svg width="12" height="12" viewBox="0 0 24 24"><path fill="var(--navy)" d="M6.6 10.8a15 15 0 0 0 6.6 6.6l2.2-2.2a1 1 0 0 1 1-.25 11 11 0 0 0 3.6.6 1 1 0 0 1 1 1V20a1 1 0 0 1-1 1A17 17 0 0 1 3 4a1 1 0 0 1 1-1h3.5a1 1 0 0 1 1 1 11 11 0 0 0 .6 3.6 1 1 0 0 1-.25 1z"/></svg>24/7 Help 202.555.0147</span>
    <span style="left:1013px"><i class="flag"></i>English <svg width="9" height="6" viewBox="0 0 9 6"><path d="M1 1l3.5 3.5L8 1" stroke="var(--navy)" stroke-width="1.5" fill="none"/></svg></span>
  </div>
  <nav class="abs nav">
    <div class="logo"><i class="dot"></i>Lumen Health</div>
    <div class="menu">
      <svg width="15" height="14" viewBox="0 0 16 14"><path fill="var(--navy)" d="M8 0l8 7h-2v7h-4V9H6v5H2V7H0z"/></svg>
      <span>ABOUT US</span><span>SERVICES</span><span>CAREERS</span><span>NEWS &amp; EVENTS</span><span>SUCCESS STORIES</span>
      <svg style="margin-left:30px" width="13" height="13" viewBox="0 0 14 14"><circle cx="6" cy="6" r="4.5" stroke="var(--navy)" stroke-width="1.6" fill="none"/><path d="M9.5 9.5L13 13" stroke="var(--navy)" stroke-width="1.6"/></svg>
    </div>
    <div class="btn-navy">CONTACT US</div>
  </nav>
</header>

<section class="hero">
  <div class="abs hero-photo" role="img" aria-label="Photo: a caregiver handing a warm drink to a smiling young woman by a snowy window"></div>
  <h1 class="abs hero-title">WHERE NEW<br>LIVES BEGIN</h1>
  <p class="abs hero-text">We provide each individual with assistance to help them lead better and<br>happier lives.</p>
  <div class="abs btn-orange" style="left:89px;top:437px;width:123px;height:44px">BOOK NOW</div>
  <div class="abs dots" style="left:89px;top:522px"><i></i><i></i><i class="on"></i><i></i></div>
</section>

<section class="insurance">
  <div class="abs photo-card" style="left:167px;top:852px;width:325px;height:379px;background:linear-gradient(135deg,#3c4a3e,#5a7fa8 45%,#e6e6ea 60%,#8a2f3b)" role="img" aria-label="Photo: two colleagues smiling while reviewing paperwork"></div>
  <h2 class="abs h2" style="left:612px;top:894px;width:460px">LUMEN WORKS WITH YOUR INSURANCE</h2>
  <p class="abs body" style="left:612px;top:982px;width:430px;font-size:13px">Among other insurances, we accept both Medicare and Medicaid, and our team is dedicated to helping you navigate the process of setting up and accessing your insurance benefits. If you need assistance with enrollment or understanding your coverage, we're here to guide you every step of the way</p>
  <div class="abs btn-orange" style="left:612px;top:1092px;width:160px;height:44px">CONTACT US TODAY</div>
</section>

<section class="impact">
  <h2 class="abs h2 center" style="left:0;top:1253px;width:1200px">OUR IMPACT</h2>
  <p class="abs body center" style="left:330px;top:1298px;width:540px">Over 200 years of service as a leading nonprofit in the DC community providing prevention, intervention, and services.</p>
  <div class="abs stat" style="left:221px;top:1376px"><b style="color:var(--orange)">60,000+</b>Visits through 28<br>Programs per Year.</div>
  <div class="abs divider" style="left:465px;top:1380px"></div>
  <div class="abs stat" style="left:493px;top:1376px"><b style="color:var(--navy)">75+</b>Collaborative Partners for<br>Service Coordination<br>and Advocacy.</div>
  <div class="abs divider" style="left:744px;top:1380px"></div>
  <div class="abs stat" style="left:757px;top:1376px"><b style="color:var(--teal)">2100+</b>Students Served<br>through SchoolBased<br>Services.</div>
</section>

<section class="services">
  <div class="abs services-bg"></div>
  <h2 class="abs h2 center" style="left:0;top:1669px;width:1200px">SERVICES WE OFFER</h2>
  <p class="abs body center" style="left:260px;top:1714px;width:680px">Each of the services we offer is tailored to our client's needs. We aim to improve the lives and help them reach their full potential.</p>
  <svg class="abs" style="left:114px;top:1991px" width="28" height="20" viewBox="0 0 28 20"><path d="M27 10H2M10 2L2 10l8 8" stroke="var(--orange)" stroke-width="2" fill="none"/></svg>
  <svg class="abs" style="left:1067px;top:1991px" width="28" height="20" viewBox="0 0 28 20"><path d="M1 10h25M18 2l8 8-8 8" stroke="#666" stroke-width="2" fill="none"/></svg>

  <article class="abs card" style="left:179px;top:1784px">
    <div class="img" style="background:linear-gradient(135deg,#e5e8ea,#9fb7cf 60%,#3c4f6a)" role="img" aria-label="Photo: a counselor taking notes with a distressed young man"></div>
    <h3>PSYCHIATRIC<br>CONSULTATIONS</h3>
    <p>We offer psychiatric consultations to help our patient's get the medication that they need.</p>
    <div class="more">CLICK HERE<span class="circ"><svg width="8" height="10" viewBox="0 0 8 10"><path d="M2 1l4 4-4 4" stroke="#fff" stroke-width="1.6" fill="none"/></svg></span></div>
  </article>
  <article class="abs card" style="left:468px;top:1784px">
    <div class="img" style="background:linear-gradient(135deg,#6c6d74,#cbb6cf 55%,#ece7ef)" role="img" aria-label="Photo: an older therapist listening to a man holding his head in his hands"></div>
    <h3>SUBSTANCE<br>ABUSE/ADDICTION</h3>
    <p>We help our clients get through a difficult time.</p>
    <div class="more">CLICK HERE<span class="circ"><svg width="8" height="10" viewBox="0 0 8 10"><path d="M2 1l4 4-4 4" stroke="#fff" stroke-width="1.6" fill="none"/></svg></span></div>
  </article>
  <article class="abs card" style="left:757px;top:1784px">
    <div class="img" style="background:linear-gradient(135deg,#efe9e4,#b8c7d6 50%,#4a4646)" role="img" aria-label="Photo: parents and a young daughter on a sofa in a family session"></div>
    <h3>FAMILY COUNSELING<br>&amp; THERAPY</h3>
    <p>We assist in mending rifts caused by familial dispute.</p>
    <div class="more">CLICK HERE<span class="circ"><svg width="8" height="10" viewBox="0 0 8 10"><path d="M2 1l4 4-4 4" stroke="#fff" stroke-width="1.6" fill="none"/></svg></span></div>
  </article>
</section>

<section class="why">
  <h2 class="abs h2" style="left:164px;top:2481px">WHY CHOOSE US</h2>
  <p class="abs body" style="left:164px;top:2533px;width:420px">We strive to be a person centered organization staffed by highly trained professionals who are dedicated to patients, families and the communities.</p>
  <p class="abs body" style="left:164px;top:2611px;width:420px">We serve by delivering quality behavioral healthcare that insures safety and preserves dignity while enhancing the well-being of those who entrust us with their care.</p>
  <div class="abs checks" style="left:164px;top:2692px">
    <div><svg width="14" height="14" viewBox="0 0 14 14"><circle cx="7" cy="7" r="7" fill="var(--orange)"/><path d="M4 7.2l2 2 4-4" stroke="#fff" stroke-width="1.5" fill="none"/></svg>Multi-Disciplinary Teams</div>
    <div><svg width="14" height="14" viewBox="0 0 14 14"><circle cx="7" cy="7" r="7" fill="var(--orange)"/><path d="M4 7.2l2 2 4-4" stroke="#fff" stroke-width="1.5" fill="none"/></svg>Highly Trained Professionals</div>
    <div><svg width="14" height="14" viewBox="0 0 14 14"><circle cx="7" cy="7" r="7" fill="var(--orange)"/><path d="M4 7.2l2 2 4-4" stroke="#fff" stroke-width="1.5" fill="none"/></svg>24/7 On-Call Service</div>
    <div><svg width="14" height="14" viewBox="0 0 14 14"><circle cx="7" cy="7" r="7" fill="var(--orange)"/><path d="M4 7.2l2 2 4-4" stroke="#fff" stroke-width="1.5" fill="none"/></svg>Quality Behavioral Healthcare</div>
  </div>
  <div class="abs photo-card" style="left:711px;top:2431px;width:325px;height:378px;background:linear-gradient(135deg,#d9d2c7,#e8c32a 40%,#a9c1df 70%,#3a3e4a)" role="img" aria-label="Photo: a caseworker in a yellow jacket reviewing papers with a man in a wheelchair"></div>
</section>

<section class="testimonials">
  <div class="abs quote-mark" aria-hidden="true">&ldquo;</div>
  <h2 class="abs h2 center" style="left:0;top:2988px;width:1200px">TESTIMONIALS</h2>
  <p class="abs body center" style="left:235px;top:3043px;width:730px">"As a working journalist for over three decades, I have witnessed and reported on the lasting impact of strong community services that empower our most vulnerable neighbors. Like so many other families, I am no stranger to the critical need of quality behavioral and mental healthcare to ensure a pathway to a brighter future for the individual and the family as a whole.</p>
  <p class="abs center" style="left:0;top:3145px;width:1200px;font-size:16px;font-weight:600;color:var(--navy)">DANIEL REYES</p>
  <div class="abs dots" style="left:587px;top:3180px;gap:3px"><i style="background:#b9bcc4"></i><i></i><i style="background:#b9bcc4"></i></div>
</section>

<footer>
  <svg class="abs" style="left:0;top:3232px" width="1200" height="204" viewBox="0 0 1200 204"><path d="M0 0H1050C1110 20 1160 110 1168 204H0Z" fill="var(--navy)"/></svg>
  <div class="abs logo" style="left:93px;top:3298px;font-size:26px;color:#fff"><i class="dot"></i>Lumen Health</div>
  <div class="abs" style="left:300px;top:3303px;font-size:12px;font-weight:600;color:#fff;line-height:23px;white-space:nowrap">
    <div>&#9742;&nbsp; (+1) 20 555 0199</div>
    <div>&#9993;&nbsp; hello@lumen.example</div>
  </div>
  <div class="abs footer-nav" style="left:479px;top:3326px"><span>HOME</span><span>ABOUT US</span><span>SERVICES</span><span>CAREERS</span><span>NEWS &amp; EVENTS</span><span>SUCCESS STORIES</span></div>
  <div class="abs" style="left:88px;top:3379px;display:flex;gap:9px"><i class="social" style="background:var(--orange)"></i><i class="social"></i><i class="social"></i><i class="social"></i></div>
  <div class="abs" style="left:561px;top:3391px;font-size:10px;color:#fff;display:flex;gap:16px;white-space:nowrap"><span>© 2025 • Lumen Health, LLC All rights reserved | Privacy Policy</span><span>Terms of Service</span><span>Privacy and Cookies</span></div>
</footer>

</body>
</html>
```